Business Card Design for Varomir Facility Services

We are looking for a Business Card Design for the Company "Varomir Facility Services."
Front side:
- Company Logo (small)
- Company Name, address, pohone, website and personal data.
- white background, for text e.g. company colors (blue or green like in the logo)
Please use following data:
Company data:
Varomir Facility Services Kostelac
Birkenhaldweg 14
6330 Cham
www.varomir-fs.ch
Person data:
Tarik Kostelac
Geschäftsführer
+41 76 519 47 83
info@varomir-fs.ch
Back side:
could be colored in blue or green
please use a big logo sing and some smaller icons to say what is all beeing offered in facility services, like cleaning, maintenance cleaning
industrial cleaning, caretaking, gardening, disposal. There is no need for everyone of the icons if there are similar or an icon is standing for more of them.
colors to use:
blue: HEX 246BB0
green: HEX 52B33E

```html
<!DOCTYPE html>
<html lang="de">
<head>
<meta charset="utf-8">
<title>Varomir Facility Services – Business Card</title>
<link href="https://fonts.googleapis.com/css2?family=Poppins:wght@400;600&display=swap" rel="stylesheet">
<style>
  :root {
    --blue: #246BB0;
    --green: #52B33E;
    --white: #ffffff;
    --backdrop: #e9e7e3;
    --shadow: rgba(0,0,0,0.28);
  }
  * { box-sizing: border-box; margin: 0; padding: 0; }
  html, body {
    width: 1125px; height: 1200px; overflow: hidden;
    background: var(--backdrop);
    font-family: "Poppins", Arial, sans-serif;
  }
  .canvas { position: relative; width: 1125px; height: 1200px; }
  .card {
    position: absolute; left: 150px; width: 826px; height: 471px;
    box-shadow: 0 4px 10px var(--shadow); overflow: hidden;
  }
  .card--front { top: 98px; background: var(--white); }
  .card--back { top: 631px; background: var(--green); }

  .front-shape { position: absolute; inset: 0; width: 100%; height: 100%; }

  .person { position: absolute; left: 52px; top: 52px; color: var(--white); }
  .person__name { font-size: 29px; font-weight: 600; line-height: 1.2; }
  .person__role { font-size: 20px; font-weight: 400; line-height: 1.2; }

  .contact { position: absolute; left: 52px; top: 244px; color: var(--white); list-style: none; }
  .contact li { display: flex; align-items: center; gap: 8px; font-size: 19px; line-height: 26px; }
  .contact svg { width: 18px; height: 18px; flex: none; }

  .address { position: absolute; left: 52px; top: 340px; color: var(--white); font-size: 19px; line-height: 25px; font-style: normal; }

  .brand { position: absolute; display: flex; align-items: center; gap: 14px; font-weight: 600; }
  .brand__dot { border-radius: 50%; flex: none; }
  .brand--front { left: 480px; top: 150px; width: 320px; color: var(--blue); font-size: 30px; line-height: 1.15; }
  .brand--front .brand__dot { width: 26px; height: 26px; background: var(--green); }
  .brand--back { left: 120px; top: 170px; width: 300px; color: var(--white); font-size: 36px; line-height: 1.15; }
  .brand--back .brand__dot { width: 34px; height: 34px; background: var(--blue); }

  .services { position: absolute; left: 440px; top: 165px; list-style: none; color: var(--white); }
  .services li { display: flex; align-items: center; gap: 10px; font-size: 20px; line-height: 25px; }
  .services svg { width: 16px; height: 16px; flex: none; }
</style>
</head>
<body>
<main class="canvas">
  <section class="card card--front" aria-label="Front side">
    <svg class="front-shape" viewBox="0 0 826 471" preserveAspectRatio="none" aria-hidden="true">
      <rect width="826" height="471" fill="var(--blue)"/>
      <path d="M470,0 C355,40 300,260 470,390 C560,455 680,470 760,471 L826,471 L826,0 Z" fill="var(--white)"/>
      <path d="M462,4 C350,50 300,265 465,395 C540,450 600,462 660,466 C580,455 520,430 472,392 C318,268 360,60 480,2 Z" fill="var(--green)"/>
      <path d="M478,2 C378,60 345,268 490,390 C560,448 680,466 760,471 C660,462 560,440 496,388 C360,270 395,70 488,0 Z" fill="var(--blue)"/>
      <path d="M488,0 C395,70 360,270 496,388 C560,440 660,462 760,471" fill="none" stroke="var(--white)" stroke-width="3"/>
    </svg>

    <div class="person">
      <h1 class="person__name">Tarik Kostelac</h1>
      <p class="person__role">Geschäftsführer</p>
    </div>

    <ul class="contact">
      <li>
        <svg viewBox="0 0 18 18"><rect x="4" y="1" width="10" height="16" rx="1.5" fill="none" stroke="var(--white)" stroke-width="1.6"/><rect x="7.5" y="14" width="3" height="1.2" fill="var(--white)"/></svg>
        +41 76 519 47 83
      </li>
      <li>
        <svg viewBox="0 0 18 18"><rect x="2" y="5" width="14" height="9" fill="var(--white)"/><path d="M2,5 L9,10.5 L16,5" fill="none" stroke="var(--blue)" stroke-width="1.3"/></svg>
        info@varomir-fs.ch
      </li>
      <li>
        <svg viewBox="0 0 18 18"><circle cx="9" cy="9" r="7.5" fill="var(--white)"/><path d="M5,5 Q8,7 7,10 Q9,12 8,15 M11,3.5 Q13,7 15,8" fill="none" stroke="var(--blue)" stroke-width="1.5"/></svg>
        www.varomir-fs.ch
      </li>
    </ul>

    <address class="address">
      Varomir Facility Services Kostelac<br>
      Birkenhaldweg 14<br>
      6330 Cham
    </address>

    <div class="brand brand--front">
      <span class="brand__dot"></span>
      <span class="brand__name">Varomir Facility Services</span>
    </div>
  </section>

  <section class="card card--back" aria-label="Back side">
    <div class="brand brand--back">
      <span class="brand__dot"></span>
      <span class="brand__name">Varomir Facility Services</span>
    </div>

    <ul class="services">
      <li><svg viewBox="0 0 16 16"><path d="M8,0 L9.3,6.7 L16,8 L9.3,9.3 L8,16 L6.7,9.3 L0,8 L6.7,6.7 Z" fill="var(--white)"/></svg>Cleaning</li>
      <li><svg viewBox="0 0 16 16"><path d="M8,0 L9.3,6.7 L16,8 L9.3,9.3 L8,16 L6.7,9.3 L0,8 L6.7,6.7 Z" fill="var(--white)"/></svg>Maintenance cleaning</li>
      <li><svg viewBox="0 0 16 16"><path d="M8,0 L9.3,6.7 L16,8 L9.3,9.3 L8,16 L6.7,9.3 L0,8 L6.7,6.7 Z" fill="var(--white)"/></svg>Industrial cleaning</li>
      <li><svg viewBox="0 0 16 16"><path d="M8,0 L9.3,6.7 L16,8 L9.3,9.3 L8,16 L6.7,9.3 L0,8 L6.7,6.7 Z" fill="var(--white)"/></svg>Caretaking</li>
      <li><svg viewBox="0 0 16 16"><path d="M8,0 L9.3,6.7 L16,8 L9.3,9.3 L8,16 L6.7,9.3 L0,8 L6.7,6.7 Z" fill="var(--white)"/></svg>Gardening</li>
      <li><svg viewBox="0 0 16 16"><path d="M8,0 L9.3,6.7 L16,8 L9.3,9.3 L8,16 L6.7,9.3 L0,8 L6.7,6.7 Z" fill="var(--white)"/></svg>Disposal</li>
    </ul>
  </section>
</main>
</body>
</html>
```